LinkedIn Banner Design for B2B Consulting Firm

Take the already developed logo (attached) and incorporate it into a creative banner design for placement on LinkedIn (the social media platform targeting business users). The banner will be used on the firm's company profile page on LinkedIn (not yet created).

```html
<!DOCTYPE html>
<html lang="en">
<head>
<meta charset="utf-8">
<title>Fractional Marketing Banner</title>
<link rel="stylesheet" href="https://fonts.googleapis.com/css2?family=Poppins:wght@300;600&display=swap">
<style>
  :root {
    --stage: #4d4d4d;
    --brand-green: #4a6e51;
    --brand-green-deep: #3f6146;
    --photo-light: #e6e6e6;
    --photo-mid: #b9b9b9;
    --photo-dark: #6e6e6e;
    --text-light: #ffffff;
  }
  html, body {
    margin: 0;
    padding: 0;
    width: 1040px;
    height: 1200px;
    overflow: hidden;
    background: var(--stage);
  }
  .cover-banner {
    position: absolute;
    left: 20px;
    top: 515px;
    width: 1000px;
    height: 170px;
    overflow: hidden;
    box-shadow: 0 4px 14px rgba(0, 0, 0, 0.35);
  }
  .cover-banner svg {
    position: absolute;
    inset: 0;
    display: block;
  }
  .headline {
    position: absolute;
    left: 642px;
    top: 44px;
    margin: 0;
    font-family: "Poppins", sans-serif;
    color: var(--text-light);
    line-height: 1.05;
    letter-spacing: 0.2px;
  }
  .headline .kicker {
    display: block;
    font-weight: 300;
    font-size: 23px;
  }
  .headline .claim {
    display: block;
    font-weight: 600;
    font-size: 24.5px;
  }
</style>
</head>
<body>
  <section class="cover-banner">
    <svg width="1000" height="170" viewBox="0 0 1000 170">
      <defs>
        <linearGradient id="photoTone" x1="0" y1="0" x2="1" y2="1">
          <stop offset="0" stop-color="var(--photo-mid)"/>
          <stop offset="0.35" stop-color="var(--photo-light)"/>
          <stop offset="0.6" stop-color="var(--photo-mid)"/>
          <stop offset="1" stop-color="var(--photo-dark)"/>
        </linearGradient>
        <linearGradient id="greenTone" x1="0" y1="0" x2="1" y2="0">
          <stop offset="0" stop-color="var(--brand-green)"/>
          <stop offset="1" stop-color="var(--brand-green-deep)"/>
        </linearGradient>
      </defs>
      <rect class="photo-area" x="0" y="0" width="640" height="170" fill="url(#photoTone)"
            role="img" aria-label="Monochrome photo of business people shaking hands in front of a city skyline with a world map network overlay"/>
      <polygon class="brand-panel" points="460,0 1000,0 1000,170 630,170" fill="url(#greenTone)"/>
    </svg>
    <h1 class="headline">
      <span class="kicker">BEST-IN-CLASS</span>
      <span class="claim">CORPORATE FRACTIONAL</span>
      <span class="claim">MARKETING SERVICES</span>
    </h1>
  </section>
</body>
</html>
```